Birchline Septic Solutions

Would like to see some single sided ones but would also like to see some double sided with one sided only being the logo. Owners name is Colin Vandro. Phone number is 555-214-0387
Services are pumping, inspections, installs, and repairs

Contact Information for Business Card

555-241-0387 Colin Vandro Maplewood, OH

```html
<!DOCTYPE html>
<html lang="en">
<head>
<meta charset="utf-8">
<title>Birchline Septic Solutions — Business Cards</title>
<link href="https://fonts.googleapis.com/css2?family=Montserrat:wght@400;700;800&display=swap" rel="stylesheet">
<style>
  :root {
    --backdrop: #474746;
    --card: #161616;
    --teal: #2fbdb8;
    --white: #ffffff;
    --muted: #e9e9e9;
  }
  * { margin: 0; padding: 0; box-sizing: border-box; }
  html, body { width: 1200px; height: 801px; overflow: hidden; }
  body {
    background: var(--backdrop);
    font-family: "Montserrat", Arial, sans-serif;
    position: relative;
  }
  .card {
    position: absolute;
    width: 510px;
    height: 292px;
    background: var(--card);
    border-radius: 16px;
    overflow: hidden;
    box-shadow: 0 14px 30px rgba(0,0,0,.35);
  }
  .card--contact { left: 60px; top: 254px; }
  .card--brand { left: 630px; top: 254px; border-bottom: 3px solid var(--teal); }

  .swoosh { position: absolute; inset: 0; width: 100%; height: 100%; }

  .wordmark {
    color: var(--white);
    font-weight: 800;
    text-transform: uppercase;
    line-height: 1;
  }
  .wordmark__name { display: block; }
  .wordmark__line { display: block; letter-spacing: .28em; }

  .card--contact .wordmark {
    position: absolute; left: 30px; top: 108px; width: 210px; text-align: center;
  }
  .card--contact .wordmark__name { font-size: 31px; letter-spacing: .01em; }
  .card--contact .wordmark__line { font-size: 11px; margin-top: 9px; }

  .divider {
    position: absolute; left: 250px; top: 40px;
    width: 1.5px; height: 150px; background: var(--teal);
  }

  .contact { position: absolute; left: 272px; top: 34px; color: var(--muted); }
  .contact__name { color: var(--teal); font-weight: 800; font-size: 21px; line-height: 1.1; }
  .contact__place { font-size: 12px; margin-top: 2px; }
  .contact__list { list-style: none; margin-top: 16px; font-size: 12px; line-height: 1.55; }
  .contact__list li { display: flex; align-items: center; gap: 7px; }
  .contact__list svg { width: 10px; height: 10px; flex: none; }
  .contact__address { font-size: 12px; line-height: 1.4; margin-top: 14px; }

  .card--brand .wordmark {
    position: absolute; left: 0; right: 0; top: 84px; text-align: center;
  }
  .card--brand .wordmark__name { font-size: 56px; letter-spacing: .01em; }
  .card--brand .wordmark__line { font-size: 17px; margin-top: 14px; }

  .tagline {
    position: absolute; left: 0; right: 0; top: 220px;
    text-align: center; color: var(--teal); font-size: 15px; font-weight: 400;
    letter-spacing: .02em;
  }
</style>
</head>
<body>

  <section class="card card--contact" aria-label="Business card, contact side">
    <svg class="swoosh" viewBox="0 0 510 292" preserveAspectRatio="none" aria-hidden="true">
      <path d="M0,292 L0,290 C30,258 90,250 200,247 C320,244 430,240 510,236 L510,292 Z" fill="var(--teal)"/>
      <path d="M0,280 C28,248 88,240 200,237 C320,234 430,230 510,226" fill="none" stroke="var(--white)" stroke-width="4"/>
    </svg>

    <div class="wordmark">
      <span class="wordmark__name">Birchline</span>
      <span class="wordmark__line">Septic Solutions</span>
    </div>

    <div class="divider"></div>

    <div class="contact">
      <p class="contact__name">Colin Vandro</p>
      <p class="contact__place">Maplewood</p>
      <ul class="contact__list">
        <li>
          <svg viewBox="0 0 10 10" aria-hidden="true"><path d="M2 0.5 L3.8 2.6 L2.8 3.8 C3.4 5.2 4.8 6.6 6.2 7.2 L7.4 6.2 L9.5 8 L8.2 9.5 C4.5 9.2 0.8 5.5 0.5 1.8 Z" fill="var(--teal)"/></svg>
          555-214-0387
        </li>
        <li>
          <svg viewBox="0 0 10 10" aria-hidden="true"><rect x="0.5" y="2" width="9" height="6.5" fill="var(--teal)"/><path d="M0.5 2 L5 5.6 L9.5 2" fill="none" stroke="var(--card)" stroke-width="1"/></svg>
          info@yourgmail.com
        </li>
        <li>
          <svg viewBox="0 0 10 10" aria-hidden="true"><circle cx="5" cy="5" r="4.5" fill="var(--teal)"/><path d="M0.5 5 H9.5 M5 0.5 C2.5 3 2.5 7 5 9.5 M5 0.5 C7.5 3 7.5 7 5 9.5" fill="none" stroke="var(--card)" stroke-width=".8"/></svg>
          www.yourwebsite.com
        </li>
      </ul>
      <p class="contact__address">Your address, City<br>State, Zip 1234</p>
    </div>
  </section>

  <section class="card card--brand" aria-label="Business card, brand side">
    <div class="wordmark">
      <span class="wordmark__name">Birchline</span>
      <span class="wordmark__line">Septic Solutions</span>
    </div>
    <p class="tagline">Services are pumping, inspections, installs, and repairs</p>
  </section>

</body>
</html>
```